Local business providing residential house cleaning services

We need a business card design that is "cute" or "cartoonish" while still maintaining a professional appeal. Tidal Sweepers is the name. We would like to use a "pin up girl" or maid next to the name with a broom or vacuum cleaner. We want the look to have a 50's American look to it. We are not sure if we want the pin up girl in a maid outfit or with a broom or vacuum cleaner but we hope some of you will be able to take these ideas and be creative. If you have any questions at all please don't hesitate to message me so that we can get the best design possible. Thank you very much and I look forward to seeing some designs! Mira Hollister

Target Market(s)

Upper class Americans that are busy and have money and want to come home to a clean house.

Industry/Entity Type

Cleaning Service

Contact Information for Business Card

Pin up girl incorporated into the card is a must.

Font styles to use
Decorative
Script

Requirements
Must have
• Pin up girl
Nice to have
• A crown used on the Q possibly.

```html
<!DOCTYPE html>
<html lang="en">
<head>
<meta charset="utf-8">
<title>Tidal Sweepers – Business Card</title>
<link rel="stylesheet" href="https://fonts.googleapis.com/css2?family=Source+Sans+3:wght@400;600&display=swap">
<style>
  :root {
    --backdrop: #1c1c1c;
    --card-white: #ffffff;
    --brand-magenta: #c300d8;
    --rule-magenta: #e39bf0;
    --ink: #444444;
    --on-magenta: #ffffff;
  }
  * { margin: 0; padding: 0; box-sizing: border-box; }
  html, body {
    width: 1200px; height: 900px; overflow: hidden;
    background: var(--backdrop);
    font-family: "Source Sans 3", Arial, sans-serif;
  }
  .stage { position: relative; width: 1200px; height: 900px; }
  .card {
    position: absolute; top: 306px; width: 440px; height: 271px;
    border-radius: 12px; overflow: hidden;
  }
  .card--front { left: 149px; background: var(--card-white); }
  .card--back { left: 608px; background: var(--brand-magenta); }

  .brand-name {
    position: absolute; font-weight: 400; line-height: 1;
    white-space: nowrap;
  }
  .brand-name span { display: block; }
  .card--front .brand-name {
    left: 158px; top: 26px; color: var(--brand-magenta);
    font-size: 38px;
  }
  .card--front .brand-name span + span { margin-top: 6px; }
  .card--front .brand-dot {
    position: absolute; left: 128px; top: 62px; width: 16px; height: 16px;
    border-radius: 50%; background: var(--brand-magenta);
  }
  .card--back .brand-name {
    left: 150px; top: 56px; color: var(--on-magenta);
    font-size: 56px;
  }
  .card--back .brand-name span + span { margin-top: 18px; }
  .card--back .brand-dot {
    position: absolute; left: 104px; top: 122px; width: 24px; height: 24px;
    border-radius: 50%; background: var(--on-magenta);
  }

  .address {
    position: absolute; left: 36px; top: 152px;
    font-size: 12.5px; line-height: 16px; color: var(--ink);
  }
  .holder {
    position: absolute; right: 30px; top: 165px; text-align: right;
  }
  .holder__name { font-size: 15.5px; font-weight: 600; color: var(--brand-magenta); line-height: 18px; }
  .holder__role { font-size: 12.5px; color: var(--ink); margin-top: 10px; line-height: 14px; }
  .rule {
    position: absolute; left: 36px; top: 187px; width: 373px; height: 1.5px;
    background: var(--rule-magenta);
  }
  .contacts {
    position: absolute; left: 36px; top: 195px; list-style: none;
    font-size: 12.5px; line-height: 16px; color: var(--ink);
  }
  .contacts li { display: flex; align-items: center; }
  .contacts svg { width: 9px; height: 9px; margin-right: 7px; fill: var(--brand-magenta); }
</style>
</head>
<body>
<main class="stage">
  <section class="card card--front" aria-label="Card front">
    <div class="brand-dot"></div>
    <div class="brand-name"><span>Tidal</span><span>Sweepers</span></div>

    <p class="address">418 Maple Grove Lane<br>Springfield, IL 62704.</p>
    <div class="holder">
      <p class="holder__name">Mira Hollister</p>
      <p class="holder__role">Managing Director</p>
    </div>
    <div class="rule"></div>
    <ul class="contacts">
      <li><svg viewBox="0 0 10 10"><path d="M2 0.5 L3.8 2.8 L2.9 4 Q4.2 6 6 7.1 L7.2 6.2 L9.5 8 L8 9.6 Q4 9 0.4 2 Z"/></svg>217-555 013 482</li>
      <li><svg viewBox="0 0 10 10"><path d="M0 2 H10 V8 H0 Z M0.8 2.6 L5 5.6 L9.2 2.6" stroke="#fff" stroke-width="0.8"/></svg>hello@tidalsweep.com</li>
      <li><svg viewBox="0 0 10 10"><circle cx="5" cy="5" r="5"/></svg>www.tidalsweep.com</li>
    </ul>
  </section>

  <section class="card card--back" aria-label="Card back">
    <div class="brand-dot"></div>
    <div class="brand-name"><span>Tidal</span><span>Sweepers</span></div>
  </section>
</main>
</body>
</html>
```